Business card design for a dynamic IT consulting company

We need a business card design for a young firm, specialized in the Telecommunications/Consulting industry. The name of the company is Quindor and Partners Business Consulting Ltd. (Short name: Quindor and Partnes)
Quindor = solve read reverse, so we aim to be uncomplicated and solution-oriented. The small pipe in our logo is also related to the word solve. So we need a new business card design, which is simple, eye catching and something non traditional (I would probably prefer a square shaped design rather than a rectangle, but open for suggestions). Attached our logo.

Target Market(s)

Usually our customers are Tier1 Telecoms providers (Q-Netra, Palorix, etc) and their executives.

Industry/Entity Type

Business

Contact Information for Business Card

Name: Bence Tolnavari
Email: b.tolnavari@quindor.hu
Web: www.quindor.hu
Mobile: +36 30 518 2769
Title: Managing Director

Optional:
Company name: Quindor and Partners Ltd.
Address: 1087 Budapest, Tolvenka str. 28/C, Hungary

Font styles to use
Other font styles liked:
• helveticaneue_medium, Prime Regular are used now.

Colors

Designer to choose colors to be used in the design.

Requirements
Must have
• I would like to have a 2 sided design.
Nice to have
• I thought if we make the logo a bit bigger (without the company name), that could go to the back with the company name below. I though, if the pipe in the logo is somehow touchable on the business card, would be nice and unique.

```html
<!DOCTYPE html>
<html lang="en">
<head>
<meta charset="utf-8">
<title>Quindor and Partners – Business Card</title>
<link href="https://fonts.googleapis.com/css2?family=Exo+2:wght@500&family=Roboto:wght@400;500&display=swap" rel="stylesheet">
<style>
  :root {
    --brand-blue: #1399d6;
    --brand-blue-soft: #2ba6dd;
    --brand-magenta: #b02f93;
    --ink-grey: #58585a;
    --paper: #ffffff;
    --backdrop: #3a3632;
  }
  html, body {
    margin: 0;
    width: 1200px;
    height: 930px;
    overflow: hidden;
    background: var(--backdrop);
  }
  .canvas {
    position: relative;
    width: 1200px;
    height: 930px;
  }
  .card {
    position: absolute;
    width: 580px;
    height: 330px;
    border-radius: 18px;
    overflow: hidden;
    box-shadow: 0 8px 20px rgba(0,0,0,.35);
  }
  .card--back {
    left: 50px;
    top: 60px;
    background: var(--brand-blue);
  }
  .card--front {
    left: 570px;
    top: 530px;
    background: var(--paper);
  }
  .wordmark {
    position: absolute;
    display: flex;
    align-items: center;
    gap: 14px;
    font-family: "Exo 2", sans-serif;
    font-weight: 500;
    white-space: nowrap;
  }
  .wordmark__square {
    width: 26px;
    height: 26px;
  }
  .card--back .wordmark {
    left: 110px;
    top: 128px;
    font-size: 44px;
    color: var(--paper);
  }
  .card--back .wordmark__square { background: var(--paper); }
  .back__web {
    position: absolute;
    right: 150px;
    bottom: 52px;
    margin: 0;
    font-family: "Roboto", sans-serif;
    font-size: 15px;
    letter-spacing: 1.5px;
    color: var(--paper);
  }
  .front__decor {
    position: absolute;
    left: 330px;
    top: 112px;
    right: 0;
    bottom: 0;
    background: linear-gradient(160deg, var(--brand-blue-soft) 0%, var(--brand-blue) 70%, #1a8fc9 100%);
  }
  .card--front .wordmark {
    left: 34px;
    top: 44px;
    font-size: 40px;
    color: var(--ink-grey);
  }
  .card--front .wordmark__square { background: var(--brand-blue); }
  .person {
    position: absolute;
    left: 70px;
    top: 168px;
    font-family: "Exo 2", sans-serif;
  }
  .person__name {
    margin: 0;
    font-size: 21px;
    font-weight: 500;
    letter-spacing: 1px;
    color: var(--brand-blue);
  }
  .person__title {
    margin: 4px 0 0;
    font-family: "Roboto", sans-serif;
    font-size: 13px;
    color: var(--ink-grey);
  }
  .contact {
    position: absolute;
    right: 30px;
    top: 150px;
    text-align: right;
    font-family: "Roboto", sans-serif;
    font-size: 12.5px;
    line-height: 17px;
    color: var(--paper);
  }
  .contact__line {
    display: flex;
    justify-content: flex-end;
    align-items: center;
    gap: 8px;
    margin: 0;
  }
  .contact__icon { width: 11px; height: 11px; }
  .contact__company {
    margin: 10px 19px 0 0;
    color: var(--brand-magenta);
    font-weight: 500;
    text-transform: uppercase;
  }
  .contact__address { margin: 0 19px 0 0; }
</style>
</head>
<body>
<main class="canvas">

  <section class="card card--back" aria-label="Card back">
    <div class="wordmark">
      <span class="wordmark__square"></span>
      <span class="wordmark__name">Quindor &amp; Partners</span>
    </div>
    <p class="back__web">www.quindor.hu</p>
  </section>

  <section class="card card--front" aria-label="Card front">
    <div class="front__decor" role="img" aria-label="Decorative flowing band in brand blue with magenta accent"></div>

    <div class="wordmark">
      <span class="wordmark__square"></span>
      <span class="wordmark__name">Quindor &amp; Partners</span>
    </div>

    <div class="person">
      <p class="person__name">BENCE TOLNAVARI</p>
      <p class="person__title">Managing Director</p>
    </div>

    <div class="contact">
      <p class="contact__line">+36 30 518 2769
        <svg class="contact__icon" viewBox="0 0 12 12"><path d="M2 1 L4.5 1 L5.5 4 L4 5 C4.8 6.6 5.4 7.2 7 8 L8 6.5 L11 7.5 L11 10 C11 10.6 10.6 11 10 11 C5 11 1 7 1 2 C1 1.4 1.4 1 2 1Z" fill="var(--brand-magenta)"/></svg>
      </p>
      <p class="contact__line">b.tolnavari@quindor.hu
        <svg class="contact__icon" viewBox="0 0 12 12"><rect x="1" y="2.5" width="10" height="7" fill="var(--brand-magenta)"/><path d="M1 2.5 L6 6.5 L11 2.5" stroke="#fff" fill="none"/></svg>
      </p>
      <p class="contact__line">www.quindor.hu
        <svg class="contact__icon" viewBox="0 0 12 12"><circle cx="6" cy="6" r="5" fill="var(--brand-magenta)"/><path d="M1 6 H11 M6 1 C3.5 4 3.5 8 6 11 M6 1 C8.5 4 8.5 8 6 11" stroke="#fff" stroke-width=".8" fill="none"/></svg>
      </p>
      <p class="contact__company">Quindor and Partners Ltd.</p>
      <p class="contact__address">1087 Budapest, Tolvenka</p>
      <p class="contact__address">str. 28/C, Hungary</p>
    </div>
  </section>

</main>
</body>
</html>
```